Wellness, Meaning, and the Inner Journey Research Program Website

Overview: This website will serve a new research program (Wellness, Meaning, and the Inner Journey) at the Harrowgate University School of Medicine. I want a clean, intuitive design that has a navigation bar, but uses icons/graphic buttons to link to the main pages. In an attached Word document, I have provided a basic information architecture for the site, understanding that this project would just generate graphics and code for the 3 pages. I highlighted the 3 pages I'd like designed.
Target market: People who want to participate in our research, or contribute grant funding to specific projects.
Number of page: The design project focuses on 3 pages, but the site must accommodate 6 pages with top-level links. See attached Word doc.
Logo and website header: Please integrate our logo in the header. I've uploaded it as a png file--both with the name of the website and with just the logo image. I imaging the logo would look great in a banner set against an image of a mountain. The two main design themes I want to see included are nature and healthcare.
Text content: I have not yet provided text. Use some dummy text.
Technical Specifications:
- Build using WordPress. We will host this site ourselves on NetHarbor using WordPress.
- The design package must be coded.
- The template must be responsive to different platforms (e.g., computer, mobile phone, iPad).
Thank you! I look forward to seeing your designs.
- Ned

```html
<!DOCTYPE html>
<html lang="en">
<head>
<meta charset="utf-8">
<title>Wellness, Meaning, and the Inner Journey – The Research Program</title>
<link rel="stylesheet" href="https://fonts.googleapis.com/css2?family=Oswald:wght@500;600&family=Heebo:wght@400;500;700&display=swap">
<style>
:root{
  --navy:#144a8a;
  --teal:#1e6b5a;
  --green:#3c8f2f;
  --leaf:#4a9a3a;
  --ink:#111;
  --body:#333;
  --white:#fff;
  --dark:#0f1512;
}
*{margin:0;padding:0;box-sizing:border-box}
html,body{width:1200px;height:3349px;overflow:hidden;background:var(--white)}
body{position:relative;font-family:"Heebo",Arial,sans-serif;color:var(--body)}
.abs{position:absolute}
h1,h2,h3,.disc-label{font-family:"Oswald","Arial Narrow",sans-serif;text-transform:uppercase;font-weight:600}

/* hero */
.hero{left:0;top:0;width:1200px;height:800px;background:linear-gradient(180deg,#8fb3cf 0%,#c9a48a 20%,#3f6b3c 38%,#1f4a36 58%,#2c5a44 75%,#7a4a2c 100%)}
.brand{left:110px;top:20px;display:flex;align-items:center;gap:12px}
.brand-dot{width:50px;height:50px;border-radius:50%;background:var(--green)}
.brand-name{font-size:15px;font-weight:700;color:var(--navy);line-height:1.2;border-left:2px solid var(--green);padding-left:10px}
.nav{left:520px;top:32px;display:flex;gap:46px;font-size:16px;font-weight:500;color:var(--ink)}
.nav a{color:inherit;text-decoration:none;padding-bottom:4px}
.nav a.current{border-bottom:2px solid var(--ink)}
.hero-title{left:115px;top:238px;font-size:56px;line-height:55px;color:var(--white);letter-spacing:.5px}
.btn-start{left:113px;top:421px;width:173px;height:50px;border-radius:25px;background:var(--white);color:var(--navy);font-weight:700;font-size:16px;display:flex;align-items:center;justify-content:center}
.arrow{top:400px;width:20px;height:30px}
.hero-curve{left:0;top:600px}
.disc{border-radius:50%;border:5px solid var(--white);box-shadow:0 4px 10px rgba(0,0,0,.25);display:flex;flex-direction:column;align-items:center;justify-content:center;color:var(--white);gap:14px}
.disc-label{font-size:27px;font-weight:500}
.disc.health{left:254px;top:545px;width:254px;height:254px;background:var(--teal)}
.disc.values{left:465px;top:520px;width:268px;height:268px;background:var(--navy);z-index:2}
.disc.spirit{left:700px;top:545px;width:254px;height:254px;background:var(--leaf)}

/* vision */
.vision-title{left:0;width:1200px;top:832px;text-align:center;font-size:41px;color:var(--ink)}
.vision-text{left:159px;top:891px;width:882px;text-align:center;font-size:14.5px;line-height:28.5px}

/* team */
.team-photo{left:0;top:1075px;width:600px;height:498px;background:linear-gradient(135deg,#d8d6d2,#b9b1a6 50%,#8d8379)}
.team-panel{left:600px;top:1075px;width:600px;height:498px;background:var(--navy);color:var(--white)}
.team-title{left:77px;top:80px;font-size:41px}
.team-text{left:77px;top:147px;width:412px;font-size:14.5px;line-height:28.3px}
.btn-outline{left:78px;top:368px;width:150px;height:42px;border:2px solid var(--white);border-radius:21px;display:flex;align-items:center;justify-content:center;font-weight:500;font-size:16px}

/* projects */
.projects-title{left:0;width:1200px;top:1648px;text-align:center;font-size:41px;color:var(--ink)}
.project{width:311px;height:308px;display:flex;align-items:flex-end;justify-content:center;padding-bottom:20px;color:var(--white);font-size:25px;font-weight:500}
.p1{left:110px;top:1728px;background:linear-gradient(180deg,#e8d2b8,#8a5a4e)}
.p2{left:444px;top:1728px;background:linear-gradient(180deg,#c7d4e4,#98a9b5 60%,#b69f88)}
.p3{left:777px;top:1728px;background:linear-gradient(180deg,#dfe4e8,#7a7670 60%,#4a4440)}
.p4{left:110px;top:2059px;background:linear-gradient(135deg,#c9c7c2,#6a7a4c 55%,#8d8c88)}
.p5{left:444px;top:2059px;background:linear-gradient(180deg,#e9a866,#b0704a 50%,#2a1e1a)}
.p6{left:777px;top:2059px;background:linear-gradient(180deg,#7e9a70,#4c6a4a 50%,#3a5a6e)}

/* faq */
.faq{left:0;top:2452px;width:1200px;height:600px;background:var(--dark)}
.faq-title{left:0;width:1200px;top:2512px;text-align:center;font-size:39px;color:var(--white)}
.faq-item{left:300px;width:598px;height:50px;background:var(--white);border-radius:25px;display:flex;align-items:center;padding-left:25px;font-size:15px;font-weight:500;color:var(--ink)}
.faq-plus{position:absolute;right:2px;top:2px;width:46px;height:46px}

/* footer */
.foot-h{font-family:"Oswald","Arial Narrow",sans-serif;font-size:15px;font-weight:500;color:var(--ink);text-transform:uppercase;top:3076px}
.field{height:39px;border:1px solid #bbb;font-size:12px;color:#777;padding-left:9px;display:flex;align-items:center;background:var(--white)}
.btn-sub{left:111px;top:3198px;width:330px;height:43px;background:var(--teal);color:var(--white);font-weight:700;font-size:17px;display:flex;align-items:center;justify-content:center}
.links{top:3101px;font-size:13.5px;line-height:26.7px;color:var(--ink);list-style:none}
.contact li{display:flex;align-items:center;gap:6px}
.rule{left:110px;top:3289px;width:978px;height:1px;background:#ddd}
.copy{left:111px;top:3309px;font-size:14.5px;color:var(--ink)}
.social{left:925px;top:3303px;display:flex;gap:11px}
.social span{width:32px;height:32px;border-radius:50%;background:var(--navy)}
.social span:nth-child(2){background:#c2185b}
.social span:nth-child(3){background:#1e88e5}
</style>
</head>
<body>

<section class="abs hero" role="img" aria-label="Mountain lake at sunrise with forested shores reflected in the water"></section>

<div class="abs brand">
  <span class="brand-dot"></span>
  <span class="brand-name">Wellness, Meaning, and the Inner Journey<br><span style="color:var(--green);font-size:12px">The Research Program</span></span>
</div>

<nav class="abs nav">
  <a class="current" href="#">Home</a><a href="#">People</a><a href="#">Projects</a><a href="#">FAQ's</a><a href="#">Resources</a><a href="#">Contact</a>
</nav>

<h1 class="abs hero-title">Wellness, Meaning,<br>and the Inner Journey<br>The Research Program</h1>
<a class="abs btn-start">Get Started</a>

<svg class="abs arrow" style="left:74px" viewBox="0 0 20 30"><path d="M14 4 5 15l9 11" fill="none" stroke="#fff" stroke-width="1.5"/></svg>
<svg class="abs arrow" style="left:1108px" viewBox="0 0 20 30"><path d="M6 4l9 11-9 11" fill="none" stroke="#fff" stroke-width="1.5"/></svg>

<svg class="abs hero-curve" width="1200" height="210" viewBox="0 0 1200 210">
  <path d="M0 170 Q600 -10 1200 170 V210 H0Z" fill="#fff"/>
  <path d="M0 170 Q600 -10 1200 170" fill="none" stroke="#3c8f2f" stroke-width="7"/>
</svg>

<div class="abs disc health">
  <svg width="72" height="72" viewBox="0 0 72 72" fill="none" stroke="#fff" stroke-width="2.5"><path d="M36 40 24 28a8 8 0 0 1 12-10 8 8 0 0 1 12 10Z"/><path d="M36 22v12M30 28h12"/><path d="M8 34v18l14 12M64 34v18L50 64M14 40l12 12M58 40 46 52"/></svg>
  <span class="disc-label">Healthcare</span>
</div>
<div class="abs disc values">
  <svg width="80" height="66" viewBox="0 0 80 66" fill="none" stroke="#fff" stroke-width="2.5"><path d="M40 2v8M20 8l5 5M60 8l-5 5"/><path d="M22 24h36l8 10-26 28-26-28Z"/><path d="M14 34h52M32 24l-6 10 14 28 14-28-6-10"/></svg>
  <span class="disc-label">Values</span>
</div>
<div class="abs disc spirit">
  <svg width="72" height="78" viewBox="0 0 72 78" fill="none" stroke="#fff" stroke-width="2.5"><path d="M36 2v8M22 6l4 6M50 6l-4 6"/><path d="M34 74V40l-8-20-10 24v30M38 74V40l8-20 10 24v30"/></svg>
  <span class="disc-label">Spiritual Life</span>
</div>

<h2 class="abs vision-title">Our Vision</h2>
<p class="abs vision-text">Lorem ipsum dolor sit amet, consectetur adipiscing elit, sed do eiusmod tempor incididunt ut labore et dolore magna aliqua. Quis ipsum suspendisse ultrices gravida. Risus commodo viverra maecenas accumsan lacus vel facilisis. Lorem ipsum dolor sit amet, consectetur adipiscing elit, sed do eiusmod tempor incididunt ut labore et dolore magna aliqua. Quis ipsum suspendisse ultrices gravida. Risus commodo viverra maecenas accumsan lacus vel facilisis.</p>

<div class="abs team-photo" role="img" aria-label="Group of smiling researchers standing together in an office"></div>
<section class="abs team-panel">
  <h2 class="abs team-title">Research Team</h2>
  <p class="abs team-text">Lorem ipsum dolor sit amet, consectetur adipiscing elit, sed do eiusmod tempor incididunt ut labore et gna aliqua. Quis ipsum suspendisse ultrices gravida. Risusmmodo viverra maecenas accumsan lacus vel facilisis. Lorum dolor sit amet, consectetur adipiscing elit, sed do eiusmod tempor incididunt ut labore et dolore magna aliqua. Quis ipsum suspendisse ultrices gravida. Risus commacus vel facilisis.</p>
  <a class="abs btn-outline">Learn More</a>
</section>

<h2 class="abs projects-title">Latest Projects</h2>
<div class="abs project p1" role="img" aria-label="Stack of balanced stones at sunset">Finibus Bonorum</div>
<div class="abs project p2" role="img" aria-label="Woman in a yoga pose on a beach">Finibus Bonorum</div>
<div class="abs project p3" role="img" aria-label="Group of women raising their arms outdoors">Finibus Bonorum</div>
<div class="abs project p4" role="img" aria-label="Moss-covered hand holding a small plant">Finibus Bonorum</div>
<div class="abs project p5" role="img" aria-label="Silhouette of a person reaching up at sunset">Finibus Bonorum</div>
<div class="abs project p6" role="img" aria-label="Older couple embracing in a green meadow">Finibus Bonorum</div>

<section class="abs faq">
  <svg width="1200" height="600" viewBox="0 0 1200 600" style="position:absolute;left:0;top:0">
    <defs><linearGradient id="forest" x1="0" y1="0" x2="0" y2="1"><stop offset="0" stop-color="#2b6b5c"/><stop offset="1" stop-color="#1d5a42"/></linearGradient></defs>
    <path d="M0 0H1200V408Q600 620 0 408Z" fill="url(#forest)"/>
    <path d="M0 408Q600 620 1200 408" fill="none" stroke="#3c8f2f" stroke-width="6"/>
  </svg>
</section>
<h2 class="abs faq-title">Frequently Asked Questions</h2>
<div class="abs faq-item" style="top:2596px">What makes this project unique?<svg class="faq-plus" viewBox="0 0 46 46"><circle cx="23" cy="23" r="22" fill="#1e6b5a"/><path d="M23 12v22M12 23h22" stroke="#fff" stroke-width="2"/></svg></div>
<div class="abs faq-item" style="top:2663px">Does this project assume that the impact of religion is always positive?<svg class="faq-plus" viewBox="0 0 46 46"><circle cx="23" cy="23" r="22" fill="#1e6b5a"/><path d="M23 12v22M12 23h22" stroke="#fff" stroke-width="2"/></svg></div>
<div class="abs faq-item" style="top:2731px">How can I collaborate?<svg class="faq-plus" viewBox="0 0 46 46"><circle cx="23" cy="23" r="22" fill="#1e6b5a"/><path d="M23 12v22M12 23h22" stroke="#fff" stroke-width="2"/></svg></div>
<div class="abs faq-item" style="top:2799px">Will Harrowgate U faculty lead all projects?<svg class="faq-plus" viewBox="0 0 46 46"><circle cx="23" cy="23" r="22" fill="#1e6b5a"/><path d="M23 12v22M12 23h22" stroke="#fff" stroke-width="2"/></svg></div>

<footer>
  <h3 class="abs foot-h" style="left:111px">Get Insights &amp; Updates</h3>
  <div class="abs field" style="left:111px;top:3107px;width:161px">Name</div>
  <div class="abs field" style="left:280px;top:3107px;width:161px">Name</div>
  <div class="abs field" style="left:111px;top:3153px;width:330px">Enter Email</div>
  <a class="abs btn-sub">SUBSCRIBE</a>

  <h3 class="abs foot-h" style="left:517px">Qucik Links</h3>
  <ul class="abs links" style="left:518px"><li>- Home</li><li>- People</li><li>- Projects</li><li>- FAQ's</li><li>- Resources</li><li>- Contact</li></ul>

  <h3 class="abs foot-h" style="left:695px">Other Links</h3>
  <ul class="abs links" style="left:696px"><li>- Code Of Conduct</li><li>- Privacy</li><li>- Cookies Policy</li><li>- Terms &amp; Conditions</li><li>- Sitemap</li></ul>

  <h3 class="abs foot-h" style="left:896px">Contact Info</h3>
  <ul class="abs links contact" style="left:897px">
    <li><svg width="10" height="13" viewBox="0 0 10 13"><path d="M5 0a5 5 0 0 0-5 5c0 4 5 8 5 8s5-4 5-8a5 5 0 0 0-5-5Zm0 7a2 2 0 1 1 0-4 2 2 0 0 1 0 4Z" fill="#111"/></svg>123 Your Adress Goes Here.</li>
    <li>CA, 1234567</li>
    <li><svg width="12" height="12" viewBox="0 0 12 12"><path d="M2.5 0 4.5 3 3.3 4.5a7 7 0 0 0 4.2 4.2L9 7.5l3 2-1 2.5C5 12 0 7 0 1Z" fill="#111"/></svg>888-888-8888</li>
    <li><svg width="12" height="10" viewBox="0 0 12 10"><path d="M0 0h12v10H0Z" fill="#111"/><path d="M0 1l6 4 6-4" fill="none" stroke="#fff"/></svg>info@wmij.org</li>
  </ul>

  <div class="abs rule"></div>
  <p class="abs copy">© 2021 &nbsp;WMIJ. All Rights Reserved.</p>
  <div class="abs social" aria-label="Social media links"><span></span><span></span><span></span><span></span></div>
</footer>

</body>
</html>
```